KBT Business Cards

We require business cards for our business. We would like a matte black back to the card, with our logo centred in the middle. The front side of the card is open to design.

Target Market(s)

Clients looking for legal services (professional)

Industry/Entity Type

Legal

Contact Information for Business Card

Doran Kelbrath
Partner
Mobile: 0461 738 524
Email: doran@kbtlaw.co
Website: www.kbtlaw.co
Level 3, 118 Wendmore Street
Sydney NSW 2000

Font styles to use
Other font styles liked:
• Avenir

Colors
f04a50
ffffff
1b1b1b

Requirements
Must have
• Black back with logo included in the centre of the card.
• Our font is Avenir.

```html
<!DOCTYPE html>
<html lang="en">
<head>
<meta charset="utf-8">
<title>Kelbrath Barrow Tane – Business Card</title>
<link rel="stylesheet" href="https://fonts.googleapis.com/css2?family=Mulish:wght@400;500;800&display=swap">
<style>
  :root {
    --brand-red: #d3214b;
    --brand-red-deep: #b3173c;
    --ink: #1b1b1b;
    --paper: #ffffff;
    --backdrop: #e9e7e4;
  }
  * { margin: 0; padding: 0; box-sizing: border-box; }
  html, body { width: 1200px; height: 902px; overflow: hidden; }
  body {
    background: var(--backdrop);
    font-family: "Mulish", "Avenir", sans-serif;
    color: var(--ink);
    position: relative;
  }
  .card {
    position: absolute;
    left: 93px; top: 159px;
    width: 899px; height: 513px;
    background: var(--paper);
    border-radius: 24px;
    overflow: hidden;
    box-shadow: 0 10px 30px rgba(0,0,0,0.12);
  }
  .brand {
    position: absolute;
    left: 110px; top: 211px;
    display: flex; align-items: center; gap: 51px;
  }
  .brand-square {
    width: 60px; height: 60px;
    background: var(--brand-red);
    flex: none;
  }
  .brand-name {
    font-weight: 800;
    font-size: 31px;
    line-height: 35px;
    color: var(--ink);
    text-transform: uppercase;
  }
  .divider {
    position: absolute;
    left: 447px; top: 144px;
    width: 2px; height: 227px;
    background: var(--brand-red);
  }
  .contact {
    position: absolute;
    left: 495px; top: 141px;
  }
  .contact-name {
    font-weight: 800;
    font-size: 25px;
    line-height: 28px;
    color: var(--brand-red);
    text-transform: uppercase;
    letter-spacing: 0.3px;
  }
  .contact-role {
    font-size: 20px;
    line-height: 23px;
    font-weight: 500;
  }
  .contact-address {
    margin-top: 23px;
    font-size: 21px;
    line-height: 28px;
    font-weight: 500;
  }
  .contact-lines {
    margin-top: 16px;
    list-style: none;
  }
  .contact-lines li {
    display: flex; align-items: center; gap: 11px;
    font-size: 21px; line-height: 30px; font-weight: 500;
  }
  .contact-icon { width: 25px; height: 25px; flex: none; }
  .accent { color: var(--brand-red); }
  .footer-rule {
    position: absolute;
    left: 0; right: 0; top: 458px;
    height: 6px;
    background: var(--ink);
  }
  .footer-band {
    position: absolute;
    left: 0; right: 0; top: 472px; bottom: 0;
    background: linear-gradient(90deg, var(--brand-red-deep), var(--brand-red));
  }
</style>
</head>
<body>
  <div class="card">
    <div class="brand">
      <div class="brand-square"></div>
      <div class="brand-name">Kelbrath<br>Barrow<br>Tane</div>
    </div>

    <div class="divider"></div>

    <div class="contact">
      <div class="contact-name">Doran Kelbrath</div>
      <div class="contact-role">Partner</div>
      <div class="contact-address">Level 3, 118 Wendmore Street<br>Sydney NSW 2000</div>
      <ul class="contact-lines">
        <li>
          <svg class="contact-icon" viewBox="0 0 28 28" aria-hidden="true">
            <circle cx="14" cy="14" r="12.5" fill="none" stroke="#d3214b" stroke-width="2"/>
            <circle cx="14" cy="14" r="10" fill="#d3214b"/>
            <rect x="10" y="7.5" width="8" height="13" rx="1.5" fill="none" stroke="#fff" stroke-width="1.6"/>
          </svg>
          0461 738 524
        </li>
        <li>
          <svg class="contact-icon" viewBox="0 0 28 28" aria-hidden="true">
            <circle cx="14" cy="14" r="12.5" fill="none" stroke="#d3214b" stroke-width="2"/>
            <circle cx="14" cy="14" r="10" fill="#d3214b"/>
            <rect x="8" y="9.5" width="12" height="9" fill="#fff"/>
            <path d="M8 9.5 L14 15 L20 9.5" fill="none" stroke="#d3214b" stroke-width="1.3"/>
          </svg>
          doran@kbtlaw.co
        </li>
        <li>
          <svg class="contact-icon" viewBox="0 0 28 28" aria-hidden="true">
            <circle cx="14" cy="14" r="12.5" fill="none" stroke="#d3214b" stroke-width="2"/>
            <circle cx="14" cy="14" r="10" fill="#d3214b"/>
            <g fill="none" stroke="#fff" stroke-width="1.2">
              <circle cx="14" cy="14" r="6"/>
              <ellipse cx="14" cy="14" rx="2.6" ry="6"/>
              <path d="M8 14 H20 M9 10.8 H19 M9 17.2 H19"/>
            </g>
          </svg>
          <span>www.<span class="accent">kbtlaw</span>.co</span>
        </li>
      </ul>
    </div>

    <div class="footer-rule"></div>
    <div class="footer-band"></div>
  </div>
</body>
</html>
```